Business Card for Industrial Distributor

We need a business card design for an industrial distributor. We sell machine parts for the manufacturing and oil industry. We would like the cards to look clean and modern but with a touch of industry.

Our colors are blue/white.

Please feel free to visit our website www.korvelpartsco.com

Target Market(s)

mexican manufacturers in the automobile/aerospace industry

Industry/Entity Type

Industrial

Colors
ffffff
0555a3

```html
<!DOCTYPE html>
<html lang="en">
<head>
<meta charset="utf-8">
<title>Korvel Business Card</title>
<link rel="stylesheet" href="https://fonts.googleapis.com/css2?family=Open+Sans:wght@400;700&display=swap">
<style>
  :root {
    --stage: #000000;
    --brand-blue: #293b8e;
    --mark-blue: #2f4fc0;
    --paper: #ffffff;
    --ink-light: #ffffff;
  }
  * { margin: 0; padding: 0; box-sizing: border-box; }
  html, body {
    width: 1200px; height: 900px; overflow: hidden;
    background: var(--stage);
    font-family: "Open Sans", Arial, sans-serif;
  }
  .stage { position: relative; width: 1200px; height: 900px; }

  .card-front {
    position: absolute; left: 265px; top: 200px;
    width: 310px; height: 502px;
    background: var(--brand-blue);
    border-radius: 64px 0 64px 0;
    color: var(--ink-light);
    text-align: center;
  }
  .front-name {
    position: absolute; top: 70px; left: 0; right: 0;
    font-size: 52px; font-weight: 700; letter-spacing: 0.5px; line-height: 1;
  }
  .person { position: absolute; top: 184px; left: 0; right: 0; }
  .person-name { font-size: 18px; font-weight: 700; line-height: 22px; }
  .person-role { font-size: 16px; font-weight: 400; line-height: 20px; }
  .contact { position: absolute; top: 284px; left: 0; right: 0; font-size: 15px; line-height: 19px; }
  .address { position: absolute; top: 394px; left: 0; right: 0; font-size: 13.5px; line-height: 19px; }

  .card-back {
    position: absolute; left: 641px; top: 200px;
    width: 308px; height: 502px;
    background: var(--paper);
    border-radius: 0 64px 0 64px;
  }
  .back-name {
    position: absolute; left: 154px; top: 205px;
    transform: translate(-50%, -50%) rotate(-90deg);
    white-space: nowrap;
    font-size: 64px; font-weight: 700; line-height: 1;
    color: var(--brand-blue);
  }
  .back-dot {
    position: absolute; left: 120px; top: 370px;
    width: 70px; height: 70px; border-radius: 50%;
    background: var(--mark-blue);
  }
  .back-web {
    position: absolute; left: 271px; top: 250px;
    transform: translate(-50%, -50%) rotate(-90deg);
    white-space: nowrap;
    font-size: 13px; color: var(--brand-blue);
  }
</style>
</head>
<body>
<main class="stage">
  <section class="card-front">
    <div class="front-name">Korvel</div>
    <div class="person">
      <p class="person-name">Marcus Hale</p>
      <p class="person-role">Director</p>
    </div>
    <div class="contact">
      <p>312-555-0142</p>
      <p>312-555-01873</p>
      <p>info@korvelparts.com</p>
    </div>
    <div class="address">
      <p>240 W. Harmon Suite 810 Chicago,</p>
      <p>Illinois 60607</p>
    </div>
  </section>

  <section class="card-back">
    <div class="back-name">Korvel</div>
    <div class="back-dot"></div>
    <div class="back-web">www.korvelpartsco.com</div>
  </section>
</main>
</body>
</html>
```